Car rental website design for a UAE car rental company

This project is about creating a new website design for a car rental company located in Dubai (United Arab Emirates), I opened the same project a few months ago but I didn't receive a lot of appealing entries so I closed it but this time I am marking the project as guaranteed to avoid such situation again, if you have already provided a design before then please re-submit again on this project so that it is considered while reviewing all the designs

A few important things:

1- We need a simple non-complex design
2- The final deliverable would be 2 screens (PSD, JPEG ... etc), the first screen is for the home page and the second screen is for an internal page
3- The home page must have a section that end users can use to rent a car online directly from the home page instead of going into some inner pages
4- The current website is very old and not very appealing so avoid creating a similar design (www.crestvane-autos.example)
5- The name is Crestvane but the company rents normal cars (no Limousin cars will be rented) so avoid adding any fancy cars in the images/graphics used in the design, just normal end users cars
6- The expected pages would be: home, About us, Our team, Strategy, Contact us and links to social media pages
7- The attachments include the company's logo and some screens from other car rental companies that provide online rentals/payments

If you have any questions please feel free to ask and please note that we will need the designs urgently

Thanks

Target Market(s)

Dubai - United Arab Emirates

Industry/Entity Type

It Company

Number of Pages Required

2 page

Font styles to use
Sans Serif

Requirements
Must have
• Check the project details
Nice to have
Should not have

```html
<!DOCTYPE html>
<html lang="en">
<head>
<meta charset="utf-8">
<title>Crestvane Rent A Car</title>
<link href="https://fonts.googleapis.com/css2?family=Roboto+Slab:wght@300;400&family=Roboto+Condensed:wght@300;400&family=Open+Sans:wght@400&display=swap" rel="stylesheet">
<style>
:root{
  --crimson:#a50d3e;
  --grey:#8a8a8a;
  --dark:#333;
  --band:#f4f4f4;
  --line:#c9c9c9;
  --white:#fff;
}
*{box-sizing:border-box;margin:0;padding:0}
html,body{width:920px;height:1200px;overflow:hidden;background:var(--white)}
body{position:relative;font-family:"Roboto Slab",serif;color:var(--dark)}
.abs{position:absolute}
/* header */
.site-header{left:0;top:0;width:920px;height:80px;background:linear-gradient(#f7f7f7,#e6e6e6);border-bottom:2px solid var(--crimson)}
.brand{left:62px;top:8px;display:flex;align-items:center;gap:8px}
.brand-mark{width:58px;height:64px;border:2px solid var(--crimson);background:#d8d8d8}
.brand-name{font-size:28px;font-weight:300;color:var(--grey);line-height:1}
.brand-sub{font-size:13px;color:var(--crimson);letter-spacing:2px;margin-left:26px;margin-top:2px}
.social{display:flex;gap:6px}
.social span{width:19px;height:19px;border-radius:50%;background:#3a6fb5;border:2px solid #dfe6ef}
.social span:nth-child(4){background:#c8402f}
.header-social{left:462px;top:13px}
.callus{left:648px;top:8px;display:flex;align-items:center;gap:6px;color:var(--crimson);font-family:"Roboto Condensed",sans-serif;font-size:16px}
.main-nav{left:462px;top:54px;display:flex;gap:19px;font-size:12.5px;color:var(--grey)}
.main-nav .active{color:var(--crimson)}
/* hero */
.hero{left:0;top:81px;width:920px;height:337px;background:linear-gradient(100deg,#1c2420 0%,#4d5a52 35%,#a7adb0 55%,#6b7a78 80%,#3d4a44 100%)}
.hero-title{left:67px;top:104px;width:380px;color:var(--white);font-family:"Roboto Condensed",sans-serif;font-size:24px;line-height:29px;font-weight:300}
.booking{left:540px;top:81px;width:317px;height:333px;background:var(--crimson);padding:3px 3px 0}
.tabs{display:flex;height:32px;align-items:center;font-size:12px;color:var(--white)}
.tab-active{background:#b5b5b5;height:32px;line-height:36px;padding:0 10px}
.tab{padding:0 10px}
.booking-form{position:relative;height:296px;background:rgba(235,235,235,.93);font-size:11px;color:#444}
.step{position:absolute;left:5px;width:19px;height:19px;border:1px solid var(--crimson);background:#fff;text-align:center;line-height:18px;font-size:11px}
.field{position:absolute;height:21px;border:1px solid #888;background:#f4f4f4;font-size:9.5px;padding:4px 5px}
.lbl{position:absolute}
.link{color:var(--crimson);text-decoration:underline}
.help{display:inline-block;width:15px;height:15px;border-radius:50%;background:#a6a6a6;color:#fff;text-align:center;font-size:9px;line-height:15px}
.box{display:inline-block;width:8px;height:8px;border:1px solid #666;margin-right:3px}
.quote{position:absolute;right:8px;bottom:0;width:103px;height:31px;background:var(--crimson);color:#fff;font-size:13px;text-align:center;line-height:31px}
/* features */
.features{left:0;top:418px;width:920px;height:208px;background:var(--band);border-top:2px solid var(--crimson)}
.feature{position:absolute;top:24px;width:190px;text-align:center}
.feature .ring{width:72px;height:72px;border-radius:50%;border:2px solid var(--grey);margin:0 auto 10px;display:flex;align-items:center;justify-content:center;background:#fff}
.feature .ring.on{border-color:var(--crimson)}
.feature h3{font-size:12px;font-weight:400;line-height:16px;color:#333}
.feature p{font-family:"Open Sans",sans-serif;font-size:11px;line-height:15.5px;margin-top:5px;color:#444}
.chev{top:92px;color:#fff;font-size:22px}
/* sections */
.section-title{left:0;width:920px;text-align:center;font-size:14.5px;font-weight:300;color:var(--grey)}
.section-title b{font-weight:400;color:var(--crimson)}
.dash{border-top:1px dashed #999;height:0}
.deal{position:absolute;top:690px;width:170px;text-align:center}
.deal .car{height:95px;border-radius:40% 40% 20% 20%/60% 60% 20% 20%}
.deal .silver{background:radial-gradient(ellipse at 50% 45%,#e2e4e6,#a9adb1 55%,#fff 72%)}
.deal .red{background:radial-gradient(ellipse at 50% 45%,#e8463f,#b81a1a 55%,#fff 72%)}
.deal .price{font-family:"Roboto Condensed",sans-serif;font-size:13px;margin-top:14px;color:#333}
.deal .price.on{color:var(--crimson)}
.sep{left:66px;width:790px;height:10px;background:radial-gradient(ellipse at top,rgba(0,0,0,.1),transparent 70%)}
.body-text{left:80px;width:760px;text-align:center;font-size:11px;line-height:16.8px;color:#333}
/* footer */
.site-footer{left:0;top:1155px;width:920px;height:45px;background:var(--crimson);color:#fff}
.foot-nav{left:62px;top:16px;display:flex;gap:14px;font-size:11.5px}
.foot-social{left:511px;top:13px}
.copy{left:666px;top:17px;font-family:"Open Sans",sans-serif;font-size:10.5px}
</style>
</head>
<body>

<header class="abs site-header">
  <div class="abs brand">
    <div class="brand-mark"></div>
    <div>
      <div class="brand-name">Crestvane</div>
      <div class="brand-sub">Rent A Car</div>
    </div>
  </div>
  <div class="abs social header-social"><span></span><span></span><span></span><span></span></div>
  <div class="abs callus">
    <svg width="28" height="34" viewBox="0 0 28 34"><path d="M4 18a10 10 0 0 1 20 0" fill="none" stroke="#666" stroke-width="3"/><rect x="2" y="17" width="6" height="10" rx="2" fill="#555"/><rect x="20" y="17" width="6" height="10" rx="2" fill="#555"/><path d="M23 27q0 5-8 5" fill="none" stroke="#a50d3e" stroke-width="2"/></svg>
    Call us at +971 4 555 0192
  </div>
  <nav class="abs main-nav"><span class="active">HOME</span><span>ABOUT US</span><span>OUR TEAM</span><span>STRATEGY</span><span>CONTACT US</span></nav>
</header>

<div class="abs hero" role="img" aria-label="Silver saloon car driving fast along a road with motion-blurred hills"></div>
<h1 class="abs hero-title">Experience An Extra Mile of comfort, pleasure and leisure From the best</h1>

<section class="abs booking">
  <div class="tabs"><span class="tab-active">Book A Car</span><span class="tab">View / Modify / Cancel A Reservation</span></div>
  <div class="booking-form">
    <div class="step" style="top:8px">1</div>
    <div class="lbl" style="left:38px;top:10px">Pick-up Location &nbsp;(City, State or Airport Code</div>
    <div class="lbl link" style="left:38px;top:28px">Previous Searches</div>
    <div class="field" style="left:38px;top:46px;width:260px">Dubai Airport - Terminal 3</div>
    <div class="lbl link" style="left:38px;top:77px">Help me find a rental location</div>
    <div class="lbl" style="left:38px;top:97px"><span class="box"></span>Return car to a different Crestvane Location &nbsp;<span class="help">?</span></div>
    <div class="step" style="top:119px">2</div>
    <div class="lbl" style="left:38px;top:120px">Pick-up Date &amp; Time</div>
    <div class="field" style="left:38px;top:140px;width:128px">26/03/2015</div>
    <div class="field" style="left:170px;top:140px;width:128px">16:00</div>
    <div class="lbl" style="left:38px;top:169px">Return Date &amp; Time</div>
    <div class="field" style="left:38px;top:189px;width:128px">26/03/2015</div>
    <div class="field" style="left:170px;top:189px;width:128px">16:00</div>
    <div class="lbl" style="left:38px;top:218px">Hire Car Type</div>
    <div class="field" style="left:38px;top:238px;width:128px">Automatic</div>
    <div class="lbl" style="left:174px;top:240px;font-size:10px"><span class="box"></span>Apply a discount Code <span class="help">?</span></div>
    <div class="quote">Get A Quote</div>
  </div>
</section>

<section class="abs features">
  <span class="abs chev" style="left:30px">‹</span>
  <span class="abs chev" style="left:878px">›</span>
  <div class="feature" style="left:59px">
    <div class="ring on"><svg width="46" height="36" viewBox="0 0 46 36"><path d="M4 16l4-9h16l4 9v8H4z" fill="#a50d3e"/><path d="M16 24l4-9h16l4 9v9H16z" fill="#a50d3e" stroke="#fff" stroke-width="2"/></svg></div>
    <h3>Wide Range Of Vehicles For City Driving or SUV's For Trips</h3>
    <p>Lorem ipsum dolor sit aonsectetuer adipiscing elied diam nonummy</p>
  </div>
  <div class="feature" style="left:275px">
    <div class="ring"><svg width="34" height="34" viewBox="0 0 34 34"><path d="M14 3h8v12L13 30 4 21z" transform="rotate(-40 17 17)" fill="#8a8a8a"/><circle cx="18" cy="10" r="2" fill="#fff"/></svg></div>
    <h3>Special 10% Discount For New Customers On The First Rent</h3>
    <p>Lorem ipsum dolor sit aonsectetuer adipiscing elied diam nonummy</p>
  </div>
  <div class="feature" style="left:480px">
    <div class="ring"><svg width="38" height="38" viewBox="0 0 38 38"><circle cx="14" cy="8" r="5" fill="#8a8a8a"/><rect x="18" y="6" width="14" height="4" fill="#8a8a8a"/><path d="M8 24l3-7h16l3 7v8H8z" fill="#8a8a8a"/></svg></div>
    <h3>Long Term Car<br>Rentals</h3>
    <p>Lorem ipsum dolor sit aonsectetuer adipiscing elied diam nonummy</p>
  </div>
  <div class="feature" style="left:685px">
    <div class="ring"><svg width="36" height="36" viewBox="0 0 36 36"><path d="M12 10h10a8 8 0 0 1 0 16h-4" fill="none" stroke="#8a8a8a" stroke-width="5"/><path d="M14 2L4 10l10 8z" fill="#8a8a8a"/></svg></div>
    <h3>Buyback Option After<br>Lease Term</h3>
    <p>Lorem ipsum dolor sit aonsectetuer adipiscing elied diam nonummy</p>
  </div>
</section>

<h2 class="abs section-title" style="top:650px">Grab the <b>Best Deal Today</b></h2>
<div class="abs dash" style="left:328px;top:673px;width:264px"></div>

<div class="deal" style="left:74px"><div class="car silver" role="img" aria-label="Silver saloon car"></div><div class="price on">From Only AED 1100 p/m</div></div>
<div class="deal" style="left:275px"><div class="car red" role="img" aria-label="Red saloon car"></div><div class="price">From Only AED 1100 p/m</div></div>
<div class="deal" style="left:477px"><div class="car silver" role="img" aria-label="Silver saloon car"></div><div class="price">From Only AED 1100 p/m</div></div>
<div class="deal" style="left:676px"><div class="car red" role="img" aria-label="Red saloon car"></div><div class="price">From Only AED 1100 p/m</div></div>

<div class="abs sep" style="top:834px"></div>

<h2 class="abs section-title" style="top:865px">Welcome to Crestvane <b>Rent A Car</b></h2>
<div class="abs dash" style="left:280px;top:888px;width:360px"></div>
<p class="abs body-text" style="top:893px">As Dubai is expected to welcome millions of tourists and visitors, car rental industry is believed to escalate more rapidly in the region. Over the past five years, demands for car rentals in Dubai has been augmenting at a healthy pace and is currently registering a growth rate of 20 to 25 percent per year. The swift economic growth and the number. Crestvane was established to bring comfort<br>and pleasure to all its clients. First rate service plus highly maintained and top...</p>
<p class="abs body-text" style="top:966px;font-size:12px">Read More</p>

<div class="abs sep" style="top:1004px"></div>

<h2 class="abs section-title" style="top:1035px"><span>Our</span> <b>Mission</b></h2>
<div class="abs dash" style="left:280px;top:1058px;width:360px"></div>
<p class="abs body-text" style="top:1071px">To be one of the leading auto leasing company in the fast growing economy and tourism industry of the emirate of Dubai &amp; play alongside with the major car rental companies in the globe.</p>
<p class="abs body-text" style="top:1108px">Crestvane vows to deliver comfort, luxury &amp; satisfaction to all our clients by providing them professional, hassle-free and first class service.</p>

<footer class="abs site-footer">
  <nav class="abs foot-nav"><span>HOME</span><span>ABOUT US</span><span>OUR TEAM</span><span>STRATEGY</span><span>CONTACT US</span></nav>
  <div class="abs social foot-social"><span></span><span></span><span></span><span></span></div>
  <div class="abs copy">© 2015 Crestvane. All Rights Reserved</div>
</footer>

</body>
</html>
```